DANCE STUDIO RECITAL FLYER DESIGN 2022

I am looking for a flyer for a dance recital that encapsulates the theme of the flyer. The rhetorical answer to "Where the River Bends Home..." is Hold Me Near but I would like this to be inferred in the design of the flyer. I am looking for something uplifting and positive through the design...I don't know what I am looking for but it needs to be vibrant, heartwarming, and emotional...maybe the world can be dipped in a heart or something with butterflies???

Here are the details...

Brightwing Dance Studio presents
Our 11th Annual Recital, "Where The River Bends Home..."
Saturday, June 25, at 4 pm
Kestrel Ridge High School 31857 Marlow Road
Alder Falls, Mi 48291

```html
<!DOCTYPE html>
<html lang="en">
<head>
<meta charset="utf-8">
<title>Brightwing Dance Studio – 11th Annual Recital</title>
<link rel="stylesheet" href="https://fonts.googleapis.com/css2?family=Anton&family=Archivo+Black&family=Montserrat:wght@600;700;800&display=swap">
<style>
  :root {
    --crimson: #8e0a2e;
    --ink: #1b1b1b;
    --gold: #fcbd2d;
    --paper: #f6f6f6;
    --backdrop: #eeeeee;
    --rule: #555555;
  }
  html, body {
    margin: 0;
    width: 783px;
    height: 1200px;
    overflow: hidden;
    background: var(--backdrop);
  }
  .flyer {
    position: absolute;
    left: 31.5px;
    top: 134px;
    width: 780px;
    height: 1010px;
    transform: scale(0.923);
    transform-origin: top left;
    background: linear-gradient(160deg, #ffffff 0%, var(--paper) 55%, #e9e9e9 100%);
    box-shadow: 0 6px 18px rgba(0,0,0,0.18);
    overflow: hidden;
    font-family: "Montserrat", sans-serif;
    color: var(--ink);
  }
  .dancer-photo {
    position: absolute;
    left: 450px;
    top: 0;
    width: 330px;
    height: 990px;
    background:
      radial-gradient(ellipse 48% 16% at 60% 50%, rgba(240,196,204,0.95), rgba(240,196,204,0) 100%),
      radial-gradient(ellipse 22% 13% at 62% 33%, rgba(222,70,120,0.8), rgba(222,70,120,0) 100%),
      linear-gradient(180deg, #ececec 0%, #e2dada 50%, #ececec 100%);
  }
  .brand {
    position: absolute;
    left: 46px;
    top: 92px;
    display: flex;
    align-items: center;
    gap: 10px;
  }
  .brand-dot {
    width: 26px; height: 26px;
    border-radius: 50%;
    background: var(--crimson);
  }
  .brand-name {
    font-weight: 700;
    font-size: 21px;
    line-height: 1.15;
    color: var(--crimson);
    letter-spacing: 1px;
  }
  .presents {
    position: absolute;
    left: 45px; top: 225px;
    font-weight: 700; font-size: 17px;
    display: flex; align-items: center; gap: 10px;
  }
  .presents-stroke {
    width: 108px; height: 4px;
    background: linear-gradient(90deg, var(--crimson), #b0523e 70%, transparent);
    border-radius: 2px;
  }
  .edition {
    position: absolute;
    left: 45px; top: 263px;
    width: 412px; height: 60px;
    border-top: 1px solid var(--rule);
    border-bottom: 1.5px solid var(--ink);
    display: flex;
    align-items: flex-end;
    gap: 8px;
    box-sizing: border-box;
    padding: 0 0 4px 10px;
  }
  .edition-our { font-weight: 700; font-size: 21px; line-height: 1; margin-bottom: 6px; }
  .edition-number { font-family: "Anton", sans-serif; font-size: 66px; line-height: 0.82; color: var(--crimson); }
  .edition-words { display: flex; flex-direction: column; font-weight: 700; font-size: 22px; line-height: 1.1; }
  .title {
    margin: 0;
    font-weight: normal;
  }
  .title-lead {
    position: absolute; left: 44px; top: 343px;
    font-family: "Archivo Black", sans-serif;
    font-size: 62px; line-height: 1; white-space: nowrap;
  }
  .title-key {
    position: absolute; left: 42px; top: 398px;
    font-family: "Anton", sans-serif;
    font-size: 160px; line-height: 1;
    color: var(--crimson);
    letter-spacing: 18px;
  }
  .band {
    position: absolute; left: 47px;
    background: var(--gold);
    width: 410px;
    text-align: center;
  }
  .title-tail {
    top: 553px; height: 74px;
    font-family: "Anton", sans-serif;
    font-size: 62px; line-height: 74px;
  }
  .divider {
    position: absolute; left: 49px; top: 655px;
    width: 405px; border-top: 1px dotted #888;
  }
  .date {
    position: absolute; left: 50px; top: 660px;
    display: flex; gap: 12px;
    font-family: "Anton", sans-serif;
    font-size: 118px; line-height: 1.02; letter-spacing: -4px;
  }
  .date-day { color: var(--crimson); }
  .date-time {
    position: absolute; left: 406px; top: 680px;
    width: 47px; height: 84px;
    background: var(--crimson);
    color: #fff;
    font-family: "Anton", sans-serif;
    font-size: 21px;
    writing-mode: vertical-rl;
    transform: rotate(180deg);
    text-align: center; line-height: 47px;
  }
  .weekday {
    top: 777px; height: 60px;
    font-family: "Archivo Black", sans-serif;
    font-size: 44px; letter-spacing: 5px; line-height: 62px;
  }
  .venue {
    position: absolute; left: 50px; top: 855px;
    width: 400px;
    display: flex; gap: 10px;
    font-weight: 700; font-size: 16.5px; line-height: 25px; letter-spacing: 0.2px;
  }
  .venue svg { margin-top: 4px; flex: none; }
  .website {
    position: absolute; left: 53px; top: 938px;
    font-weight: 700; font-size: 16px;
  }
  .footer-band {
    position: absolute; left: 0; bottom: 0;
    width: 100%; height: 20px;
    background: var(--crimson);
  }
</style>
</head>
<body>
  <main class="flyer">
    <div class="dancer-photo" role="img" aria-label="Ballerina on pointe with arms raised, in a pink leotard and pale tulle tutu, over a soft grey backdrop"></div>

    <div class="brand">
      <span class="brand-dot"></span>
      <span class="brand-name">BRIGHTWING<br>DANCE STUDIO</span>
    </div>

    <div class="presents">PRESENTS <span class="presents-stroke"></span></div>

    <div class="edition">
      <span class="edition-our">OUR</span>
      <span class="edition-number">11</span>
      <span class="edition-words"><span>TH</span><span>ANNUAL RECITAL</span></span>
    </div>

    <h1 class="title">
      <span class="title-lead">WHERE THE</span>
      <span class="title-key">RIVER</span>
      <span class="band title-tail">BENDS HOME</span>
    </h1>

    <div class="divider"></div>

    <div class="date">
      <span class="date-day">25</span>
      <span class="date-month">JUNE</span>
    </div>
    <span class="date-time">AT 4 PM</span>
    <div class="band weekday">SATURDAY</div>

    <div class="venue">
      <svg width="18" height="26" viewBox="0 0 18 26" aria-hidden="true">
        <path d="M9 1C4.6 1 1 4.5 1 8.9 1 15 9 25 9 25s8-10 8-16.1C17 4.5 13.4 1 9 1z" fill="var(--crimson)"/>
        <circle cx="9" cy="9" r="3.4" fill="#fff"/>
      </svg>
      <span>Kestrel Ridge High School 31857 Marlow Road<br>Alder Falls, Mi 48291</span>
    </div>

    <div class="website">www.brightwingdance.com</div>

    <div class="footer-band"></div>
  </main>
</body>
</html>
```